Graphic Design of Business Process

We require an eye-catching, sophisticated design of 2 business processes (attached), that will be used digitally AND for print (to be put on walls in our office).

The basic layout is attached. We require a creative, professional designer to re-design these so that they look appealing but still able to grasp all the information.

We will require vector files and editable project files for final delivery. You may refer to our website (quillharbourworks.com.au) for an indication of our brand.

If you have any questions, please ask.

Thank you.

```html
<!DOCTYPE html>
<html lang="en">
<head>
<meta charset="utf-8">
<title>Sales to Content Funnel and Content Hierarchy</title>
<link href="https://fonts.googleapis.com/css2?family=League+Spartan:wght@700&family=Oswald:wght@300;400;500;600&display=swap" rel="stylesheet">
<style>
  :root {
    --ink: #111111;
    --maroon: #5b0f14;
    --ground: #3a2216;
    --aware: #1b8fc5;
    --aware-side: #27a8e0;
    --aware-soft: #97c4e3;
    --aware-text: #1c2f78;
    --consider: #f6961f;
    --consider-dark: #ee7b25;
    --consider-soft: #efbb85;
    --consider-text: #c3262d;
    --action: #ee3a45;
    --action-light: #f2645d;
    --action-soft: #e8948a;
    --offer: #fff200;
    --hero: #3f51a8;
    --hero-dark: #2e3b8f;
    --hub: #b2439c;
    --hub-dark: #7d2473;
    --hygiene: #f5a020;
    --hygiene-light: #fdbf3f;
    --card: #f4f6f7;
    --card-fold: #e3e5e6;
    --white: #ffffff;
  }
  html, body {
    margin: 0;
    padding: 0;
    width: 1196px;
    height: 1200px;
    overflow: hidden;
    background: var(--white);
  }
  .artboard { display: block; width: 1196px; height: 1200px; }
  .display { font-family: "League Spartan", "Montserrat", sans-serif; font-weight: 700; }
  .condensed { font-family: "Oswald", "Arial Narrow", sans-serif; }
  .stage-title { font-weight: 600; font-size: 54px; fill: var(--white); }
  .stage-sub { font-weight: 400; font-size: 25px; }
  .stage-note { font-weight: 300; font-size: 17px; fill: var(--white); }
  .side-head { font-weight: 600; font-size: 23px; fill: var(--maroon); }
  .side-note { font-weight: 400; font-size: 17px; fill: var(--maroon); }
  .loop-label { font-weight: 600; font-size: 23px; fill: var(--maroon); }
  .brand-mark { font-size: 24px; letter-spacing: 4px; }
  .hex-label { font-weight: 600; font-size: 34px; }
  .card-label { font-weight: 600; font-size: 32px; }
</style>
</head>
<body>
<svg class="artboard" viewBox="0 0 1496 1500" xmlns="http://www.w3.org/2000/svg" aria-label="Sales to content funnel and content hierarchy">
  <defs>
    <linearGradient id="funnel-sky" x1="0" y1="0" x2="0" y2="1">
      <stop offset="0" stop-color="#fde3de"/>
      <stop offset="1" stop-color="#fbe9e5"/>
    </linearGradient>
    <linearGradient id="hierarchy-sky" x1="0" y1="0" x2="1" y2="1">
      <stop offset="0" stop-color="#aee0f7"/>
      <stop offset="0.5" stop-color="#eef8fd"/>
      <stop offset="1" stop-color="#a9def6"/>
    </linearGradient>
  </defs>

  <!-- Funnel section -->
  <g class="funnel">
    <rect width="1496" height="722" fill="url(#funnel-sky)"/>
    <text class="display" x="748" y="108" text-anchor="middle" font-size="50" fill="var(--ink)">SALES —&gt; CONTENT FUNNEL</text>

    <polygon points="385,138 1095,138 1405,665 68,665" fill="#ddd3d1"/>

    <polygon class="band-aware" points="385,150 795,150 885,310 475,310" fill="var(--aware)"/>
    <polygon points="795,150 1095,150 1185,310 885,310" fill="var(--aware-soft)"/>
    <polygon points="385,150 475,310 270,665 85,665" fill="var(--aware-side)"/>

    <polygon class="band-consider" points="475,310 885,310 985,485 580,485" fill="var(--consider)"/>
    <polygon points="885,310 1185,310 1285,485 985,485" fill="var(--consider-soft)"/>
    <polygon points="475,310 580,485 455,665 240,665" fill="var(--consider-dark)"/>
    <polygon points="490,330 580,485 460,665 270,665" fill="var(--consider)"/>

    <polygon class="band-action" points="580,485 985,485 1095,665 455,665" fill="var(--action)"/>
    <polygon points="985,485 1285,485 1395,665 1095,665" fill="var(--action-soft)"/>
    <polygon points="580,485 685,665 470,665" fill="var(--action-light)"/>

    <rect x="0" y="665" width="1496" height="57" fill="var(--ground)"/>

    <!-- Stage icons -->
    <circle cx="373" cy="320" r="58" fill="var(--white)" fill-opacity="0.18" role="img" aria-label="Icon of a head with an idea target"/>
    <g class="icon-branch" fill="none" stroke="var(--white)" stroke-width="12" stroke-linecap="round" stroke-linejoin="round">
      <circle cx="460" cy="530" r="14"/>
      <path d="M460 516 V455"/>
      <path d="M440 440 L460 455 L460 455"/>
      <path d="M447 516 Q430 495 408 490"/>
      <path d="M473 516 Q490 495 512 490"/>
    </g>
    <polygon points="460,438 476,462 444,462" fill="var(--white)"/>
    <polygon points="402,478 420,500 398,503" fill="var(--white)"/>
    <polygon points="518,478 500,500 522,503" fill="var(--white)"/>
    <circle cx="565" cy="600" r="50" fill="var(--white)" fill-opacity="0.18" role="img" aria-label="Icon of two hands offering a card"/>

    <!-- Awareness -->
    <text class="condensed stage-title" x="568" y="205" text-anchor="middle">AWARENESS</text>
    <text class="condensed stage-sub" x="472" y="238" fill="var(--aware-text)">IDENTIFY PROBLEM/NEED</text>
    <text class="condensed stage-note" x="487" y="271">- ASPIRATIONAL</text>
    <text class="condensed stage-note" x="487" y="295">- MARKET THE OUTCOME NOT PRODUCT</text>
    <text class="condensed side-head" x="870" y="218">PROBLEM &amp; SOLUTION</text>
    <text class="condensed side-note" x="893" y="249">SUBJECT SHOWING</text>
    <text class="condensed side-note" x="893" y="273">SYMPTOMS OF PROBLEM</text>

    <!-- Consideration -->
    <text class="condensed stage-title" x="690" y="370" text-anchor="middle">CONSIDERATION</text>
    <text class="condensed stage-sub" x="566" y="405" fill="var(--consider-text)">EVALUATE ALTERNATIVES</text>
    <text class="condensed stage-note" x="574" y="435">- WHY IS THIS SOLUTION BETTER THAN OTHERS</text>
    <text class="condensed stage-note" x="574" y="461">- HOW IS THIS PROVIDER GOING TO SOLVE MY NEED</text>
    <text class="condensed side-head" x="952" y="364">PROVIDERS &amp;</text>
    <text class="condensed side-head" x="952" y="394">TYPES OF SOLUTION</text>
    <text class="condensed side-note" x="970" y="422">SUBJECT GIVES NAME TO PROBLEM</text>

    <!-- Action -->
    <text class="condensed stage-title" x="802" y="545" text-anchor="middle">ACTION/DECISION</text>
    <text class="condensed stage-sub" x="660" y="584" fill="var(--offer)">PRESENT AN OFFER</text>
    <text class="condensed stage-note" x="675" y="623">- WHICH PROVIDER?</text>
    <text class="condensed side-head" x="1082" y="568">CONVERT &amp; RETAIN</text>

    <!-- Word of mouth loop -->
    <g class="loop" fill="none" stroke="var(--maroon)" stroke-width="4">
      <polyline points="1120,205 1180,205 1215,262"/>
      <polyline points="1160,347 1240,347"/>
      <polyline points="1008,522 1372,522 1330,453"/>
    </g>
    <g fill="var(--maroon)">
      <polygon points="1105,205 1128,188 1128,222"/>
      <polygon points="1143,347 1166,330 1166,364"/>
      <polygon points="988,522 1008,505 1008,539"/>
    </g>
    <text class="condensed loop-label" transform="translate(1214,272) rotate(58)">WOM &amp; REFERRAL</text>

    <text class="display brand-mark" x="1390" y="694" text-anchor="end" fill="var(--white)">QUILL HARBOUR WORKS</text>
  </g>

  <!-- Hierarchy section -->
  <g class="hierarchy">
    <rect x="342" y="750" width="810" height="708" fill="url(#hierarchy-sky)"/>
    <path d="M472 750 H1022 V865 Q1022 905 982 905 H512 Q472 905 472 865 Z" fill="#e6f5fc"/>
    <text class="display" x="748" y="868" text-anchor="middle" font-size="44" fill="var(--ink)">CONTENT HIERARCHY</text>
    <rect x="505" y="876" width="485" height="6" fill="var(--hygiene)"/>

    <!-- Decorative connectors -->
    <g fill="none" stroke-width="4">
      <polyline points="548,945 630,995 712,945" stroke="var(--hub)"/>
      <polyline points="785,945 866,995 948,945" stroke="#e6287a"/>
      <polyline points="548,1128 630,1078 712,1128" stroke="var(--hub)"/>
      <polyline points="785,1128 866,1078 948,1128" stroke="#e6287a"/>
    </g>

    <!-- Cards -->
    <g class="card card-hero">
      <rect x="406" y="1080" width="210" height="280" fill="var(--card)"/>
      <polygon points="560,1080 616,1080 616,1200" fill="var(--card-fold)"/>
      <polygon points="406,1310 450,1352 572,1352 616,1310 616,1360 406,1360" fill="var(--hero)"/>
      <text class="condensed card-label" x="511" y="1210" text-anchor="middle" fill="var(--hero)">TENTPOLE</text>
      <text class="condensed card-label" x="511" y="1252" text-anchor="middle" fill="var(--hero)">CAMPAIGNS</text>
    </g>
    <g class="card card-hub">
      <rect x="642" y="1080" width="210" height="280" fill="var(--card)"/>
      <polygon points="796,1080 852,1080 852,1200" fill="var(--card-fold)"/>
      <polygon points="642,1310 686,1352 808,1352 852,1310 852,1360 642,1360" fill="var(--hub)"/>
      <text class="condensed card-label" x="747" y="1210" text-anchor="middle" fill="var(--hub)">REGULAR</text>
      <text class="condensed card-label" x="747" y="1252" text-anchor="middle" fill="var(--hub)">“PUSH”</text>
      <text class="condensed card-label" x="747" y="1294" text-anchor="middle" fill="var(--hub)">CONTENT</text>
    </g>
    <g class="card card-hygiene">
      <rect x="878" y="1080" width="210" height="280" fill="var(--card)"/>
      <polygon points="1032,1080 1088,1080 1088,1200" fill="var(--card-fold)"/>
      <polygon points="878,1310 922,1352 1044,1352 1088,1310 1088,1360 878,1360" fill="var(--hygiene)"/>
      <text class="condensed card-label" x="983" y="1210" text-anchor="middle" fill="var(--hygiene)">ALWAYS-ON</text>
      <text class="condensed card-label" x="983" y="1252" text-anchor="middle" fill="var(--hygiene)">“PULL”</text>
      <text class="condensed card-label" x="983" y="1294" text-anchor="middle" fill="var(--hygiene)">CONTENT</text>
    </g>

    <!-- Connecting band -->
    <polygon points="395,985 630,985 630,1075 395,1075" fill="var(--hero-dark)"/>
    <rect x="630" y="985" width="240" height="90" fill="var(--hub-dark)"/>
    <polygon points="870,985 1100,1000 1100,1065 870,1075" fill="var(--hygiene-light)"/>

    <!-- Hexagons -->
    <g class="hex hex-hero">
      <polygon points="512,932 597,981 597,1079 512,1128 427,1079 427,981" fill="var(--hero)"/>
      <polygon points="512,955 577,992.5 577,1067.5 512,1105 447,1067.5 447,992.5" fill="var(--white)" stroke="#5566b5" stroke-width="6"/>
      <text class="condensed hex-label" x="512" y="1042" text-anchor="middle" fill="var(--hero)">HERO</text>
    </g>
    <g class="hex hex-hub">
      <polygon points="748,932 833,981 833,1079 748,1128 663,1079 663,981" fill="var(--hub)"/>
      <polygon points="748,955 813,992.5 813,1067.5 748,1105 683,1067.5 683,992.5" fill="var(--white)" stroke="#c25cac" stroke-width="6"/>
      <text class="condensed hex-label" x="748" y="1042" text-anchor="middle" fill="var(--hub)">HUB</text>
    </g>
    <g class="hex hex-hygiene">
      <polygon points="985,932 1070,981 1070,1079 985,1128 900,1079 900,981" fill="var(--hygiene)"/>
      <polygon points="985,955 1050,992.5 1050,1067.5 985,1105 920,1067.5 920,992.5" fill="var(--white)" stroke="#c98a2a" stroke-width="6"/>
      <text class="condensed hex-label" x="985" y="1042" text-anchor="middle" fill="var(--hygiene)">HYGIENE</text>
    </g>

    <text class="display brand-mark" x="748" y="1420" text-anchor="middle" fill="var(--ink)">QUILL HARBOUR WORKS</text>
  </g>
</svg>
</body>
</html>
```